Business card design

I am open to ideas. I was thinking of a vertical design, turning the name 90 degrees and placing it on the left edge, then some clipped portion of the fabulous tree with contact info on the bottom -- special emphasis on Web address:WhimBeads.comFor All Your Beading Needs121 E. Cotati AveCotati, CA 94931(707) 664-8343

```html
<!DOCTYPE html>
<html lang="en">
<head>
<meta charset="utf-8">
<title>Fern Glass Co – Business Card</title>
<link rel="stylesheet" href="https://fonts.googleapis.com/css2?family=Oswald:wght@500&family=Lato:wght@400&family=Playfair+Display:ital@1&display=swap">
<style>
  :root {
    --backdrop: #8a8a8a;
    --card-light: #ffffff;
    --card-dark: #000000;
    --ink: #2b2b2b;
    --rule: #9a9a9a;
    --mark-light: #d6d6d6;
    --mark-dark: #3a3a3a;
    --web-purple: #5b2d8e;
    --web-green: #1f6b3a;
    --web-red: #e0202a;
  }
  html, body { margin: 0; padding: 0; overflow: hidden; }
  body {
    width: 1200px; height: 1200px;
    background: var(--backdrop);
    position: relative;
    font-family: "Lato", sans-serif;
  }
  .card {
    position: absolute;
    box-shadow: 2px 3px 6px rgba(0,0,0,0.35);
  }
  .card--front { left: 234px; top: 310px; width: 364px; height: 594px; background: var(--card-light); }
  .card--back  { left: 627px; top: 310px; width: 369px; height: 596px; background: var(--card-dark); }

  .brand-mark {
    position: absolute;
    width: 120px; height: 120px;
    border-radius: 50%;
    left: 50%; margin-left: -60px;
  }
  .card--front .brand-mark { top: 105px; background: var(--mark-light); }
  .card--back .brand-mark  { top: 218px; background: var(--mark-dark); }

  .brand-name {
    position: absolute; left: 0; right: 0;
    text-align: center;
    font-family: "Lato", sans-serif;
    font-weight: 400;
    font-size: 30px;
    letter-spacing: 0.5px;
  }
  .card--front .brand-name { top: 244px; color: var(--ink); }
  .card--back .brand-name  { top: 360px; color: #ffffff; }

  .phone {
    position: absolute; left: 0; right: 0; top: 340px;
    text-align: center;
    font-family: "Oswald", sans-serif; font-weight: 500;
    font-size: 29px; color: var(--ink);
  }
  .website {
    position: absolute; left: 0; right: 0; top: 389px;
    text-align: center;
    font-family: "Oswald", sans-serif; font-weight: 500;
    font-size: 29px;
  }
  .website .prefix { color: var(--web-purple); }
  .website .domain { color: var(--web-green); }
  .website .suffix { color: var(--web-red); }

  .rule {
    position: absolute; left: 84px; width: 195px; height: 1px;
    background: var(--rule);
  }
  .rule--top { top: 441px; }
  .rule--bottom { top: 507px; }

  .address {
    position: absolute; left: 0; right: 0; top: 451px;
    text-align: center;
    font-size: 19px; line-height: 24px; color: var(--ink);
  }
  .tagline {
    position: absolute; left: 0; right: 0; top: 518px;
    text-align: center;
    font-family: "Playfair Display", serif; font-style: italic;
    font-size: 24px; color: var(--ink);
  }
</style>
</head>
<body>
  <section class="card card--front">
    <div class="brand-mark" aria-hidden="true"></div>
    <div class="brand-name">Fern Glass Co</div>
    <div class="phone">(707) 555-0192</div>
    <div class="website"><span class="prefix">www.</span><span class="domain">FernGlassco</span><span class="suffix">.com</span></div>
    <div class="rule rule--top"></div>
    <div class="address">348 W. Brindle Ave<br>Alder Vale, CA 94938</div>
    <div class="rule rule--bottom"></div>
    <div class="tagline">For All Your Beading Needs</div>
  </section>

  <section class="card card--back">
    <div class="brand-mark" aria-hidden="true"></div>
    <div class="brand-name">Fern Glass Co</div>
  </section>
</body>
</html>
```